Luxury WordPress Website for CORALBASINS

I need a professional WordPress website for Coral Basins. The site should be modern, visually appealing, and user-friendly, reflecting the brand’s luxury and premium identity. It must include a homepage, product/service pages, contact form, and be responsive on both desktop and mobile devices. The design should allow for easy updates and integration of future content, while maintaining a polished and professional look.

Target Market(s)

swimmingpool & spa

Industry/Entity Type

Swimmingpool

Coding

Coded - Design and coding required

Font styles to use
Other font styles liked:
• HaboroSoft

Requirements
Must have
• Exclusive appearance
Nice to have
• • A logo that subtly incorporates water or pool elements. • A color palette that reflects luxury, elegance, and relaxation. • Clean and modern typography that is easy to read across all media. • Iconography or design elements that convey premium quality. • A versatile design that can be adapted for social media, merchandise, and promotional materials. • Optional: A tagline that emphasizes luxury and high-end pool experiences.

```html
<!DOCTYPE html>
<html lang="en">
<head>
<meta charset="utf-8">
<title>Coral Basins – Luxury Pool Design</title>
<link href="https://fonts.googleapis.com/css2?family=Lato:wght@400;700;900&display=swap" rel="stylesheet">
<style>
:root{
  --navy:#0f2d5c;
  --navy-deep:#0c2650;
  --accent:#5ab4e0;
  --accent-soft:#7cc4ea;
  --ink:#1f2a37;
  --muted:#3d4652;
  --mist:#ebedf1;
  --card:#f4f3ef;
  --white:#ffffff;
}
*{box-sizing:border-box;margin:0;padding:0}
html,body{width:1200px;height:4812px;overflow:hidden;background:var(--white)}
body{font-family:"Lato",sans-serif;color:var(--ink);position:relative}
.abs{position:absolute}
section,header,footer{position:absolute;left:0;width:1200px;overflow:hidden}
.btn{position:absolute;display:flex;align-items:center;justify-content:center;font-weight:700;font-size:17px;color:var(--white);background:var(--accent);border-radius:3px;text-decoration:none}
.btn--navy{background:var(--navy)}
.heading{position:absolute;font-weight:900;color:var(--navy);text-transform:uppercase;letter-spacing:.3px;line-height:1}
.rule{position:absolute;height:4px;background:var(--accent);border-radius:2px}
.photo{position:absolute}

/* header */
.site-header{top:0;height:110px;background:var(--white)}
.brand{left:110px;top:22px;display:flex;align-items:center;gap:12px}
.brand__dot{width:40px;height:40px;border-radius:50%;background:var(--accent)}
.brand__name{font-size:25px;font-weight:900;color:var(--navy);line-height:1}
.brand__tag{font-size:12px;color:var(--accent);margin-top:4px}
.nav a{position:absolute;top:37px;height:34px;line-height:34px;font-size:15px;color:var(--ink);text-decoration:none}
.nav .is-active{background:var(--accent);color:var(--white);padding:0 12px;border-radius:3px}

/* hero */
.hero{top:110px;height:600px;background:linear-gradient(160deg,#3f5a3d 0%,#2f7a92 45%,#1f9fc4 70%,#2aa6c9 100%)}
.hero__panel{left:112px;top:0;width:471px;height:600px;background:rgba(20,50,95,.78)}
.hero__title{left:112px;top:95px;width:471px;text-align:center;color:var(--white);font-weight:900;font-size:52px;line-height:70px}
.hero__text{left:150px;top:328px;width:395px;text-align:center;color:var(--white);font-size:23px;line-height:34px}
.play{left:858px;top:267px;width:64px;height:64px;border-radius:50%;background:rgba(90,180,224,.9);border:3px solid rgba(255,255,255,.6)}

/* about */
.about{top:710px;height:724px}
.body-text{position:absolute;font-size:16px;line-height:25.6px;color:var(--muted);text-align:justify}

/* collection */
.collection{top:1434px;height:874px;background:var(--mist)}
.center-text{position:absolute;left:0;width:1200px;text-align:center}
.slide-card{left:607px;top:459px;width:421px;height:251px;background:var(--card);border:2px solid var(--accent-soft);outline:6px solid var(--card)}
.pager{position:absolute;font-size:12px;color:var(--muted)}

/* cta */
.cta{top:2308px;height:443px;background:linear-gradient(120deg,#6fbfe6 0%,#5fb4df 50%,#78c6ea 100%)}

/* testimonials */
.reviews{top:2751px;height:613px}
.arrow{position:absolute;width:32px;height:32px;border-radius:50%;background:var(--accent)}
.review{position:absolute;top:251px;width:468px;height:297px;background:var(--white);border:1px solid #e3e6ea;box-shadow:0 2px 8px rgba(15,45,92,.12);border-radius:3px}
.review p{position:absolute;left:35px;top:34px;width:405px;font-size:16px;line-height:29px;color:var(--muted)}
.avatar{position:absolute;left:32px;top:185px;width:78px;height:78px;border-radius:50%;background:linear-gradient(135deg,#6b5a48,#c79a7b)}
.review__name{position:absolute;left:125px;top:196px;font-size:21px;color:var(--accent)}
.review__role{position:absolute;left:125px;top:228px;font-size:16px;color:var(--muted)}

/* gallery */
.gallery{top:3364px;height:987px}

/* footer */
.site-footer{top:4351px;height:461px;background:var(--navy-deep);color:var(--white)}
.foot-h{position:absolute;top:104px;font-size:20px;font-weight:700;color:var(--accent)}
.foot-l{position:absolute;font-size:14px;color:var(--white);line-height:20px}
.social{position:absolute;top:300px;width:24px;height:24px;border:2px solid var(--white);border-radius:4px}
.social.is-active{top:296px;width:36px;height:36px;background:var(--accent);border-color:var(--accent)}
</style>
</head>
<body>

<header class="site-header">
  <div class="brand abs">
    <span class="brand__dot"></span>
    <div><div class="brand__name">Coral Basins</div><div class="brand__tag">Luxury. Precision. Water.</div></div>
  </div>
  <nav class="nav">
    <a class="is-active" style="left:490px">Home</a>
    <a style="left:600px">About Us</a>
    <a style="left:723px">Services</a>
    <a style="left:837px">Contact Us</a>
  </nav>
  <a class="btn" style="left:948px;top:35px;width:140px;height:42px">Get a Quote</a>
</header>

<section class="hero" role="img" aria-label="Luxury pool with sun loungers and umbrellas beside a hedge">
  <div class="hero__panel abs"></div>
  <h1 class="hero__title abs">REDEFINING<br>LUXURY<br>POOL DESIGN</h1>
  <p class="hero__text abs">Handcrafted excellence for those who demand perfection in design, durability, and elegance.</p>
  <a class="btn" style="left:250px;top:466px;width:193px;height:41px">Explore Our Pools</a>
  <div class="play abs"><svg width="58" height="58" viewBox="0 0 58 58"><path d="M23 18 L40 29 L23 40Z" fill="#fff"/></svg></div>
</section>

<section class="about">
  <h2 class="heading" style="left:110px;top:122px;font-size:44px">About Us</h2>
  <div class="rule" style="left:112px;top:172px;width:56px"></div>
  <p class="body-text" style="left:110px;top:206px;width:460px">Lorem ipsum dolor sit amet, consectetur adipiscing elit, sed do eiusmod tempor incididunt ut labore et dolore magna aliqua. Ut enim ad minim veniam, quis nostrud exercitation ullamco laboris nisi ut aliquip ex ea commodo consequat. Duis aute irure dolor in reprehenderit in voluptate velit esse cillum dolore eu fugiat nulla pariatur.</p>
  <p class="body-text" style="left:110px;top:396px;width:460px">Sed ut perspiciatis unde omnis iste natus error sit voluptatem accusantium doloremque laudantium, totam rem aperiam, eaque ipsa quae ab illo inventore veritatis et quasi architecto beatae vitae dicta sunt explicabo.</p>
  <a class="btn" style="left:110px;top:540px;width:142px;height:42px">Read More</a>
  <div class="photo" role="img" aria-label="Gazebo with curtains beside an infinity pool facing the sea" style="left:663px;top:103px;width:423px;height:503px;background:linear-gradient(180deg,#1f63c9 0%,#3b8de0 40%,#1d5fa8 60%,#5aa9d9 100%)"></div>
</section>

<section class="collection">
  <h2 class="heading center-text" style="top:98px;font-size:42px">Pools Crafted for Perfection</h2>
  <div class="rule" style="left:572px;top:149px;width:58px"></div>
  <p class="center-text" style="top:178px;font-size:16px;line-height:25px;color:var(--muted)">Handcrafted excellence for those who demand perfection in design,<br>durability, and elegance.</p>
  <div class="photo" role="img" aria-label="Hillside villa pool" style="left:0;top:317px;width:120px;height:389px;background:linear-gradient(180deg,#4b7a3c,#2d6fa8)"></div>
  <div class="photo" role="img" aria-label="Pool with fire feature and lawn at dusk" style="left:193px;top:269px;width:575px;height:387px;background:linear-gradient(180deg,#c98aa0 0%,#3f8a3a 35%,#1f7fb2 75%,#2a6d95 100%)"></div>
  <div class="photo" role="img" aria-label="Evening terrace pool with loungers" style="left:1090px;top:317px;width:110px;height:389px;background:linear-gradient(180deg,#3b5a3a,#5a6a5a)"></div>
  <div class="slide-card abs">
    <h3 style="position:absolute;top:30px;width:100%;text-align:center;font-size:25px;font-weight:700;color:var(--navy)">CUSTOM LUXURY POOLS</h3>
    <p style="position:absolute;left:45px;top:77px;width:330px;text-align:center;font-size:15px;line-height:23px;color:var(--muted)">Excepteur sint occaecat cupidatat non proident, sunt in culpa qui officia deserunt mollit anim id est laborum.</p>
    <a class="btn" style="left:139px;top:174px;width:140px;height:41px">View Details</a>
  </div>
  <span class="pager" style="left:351px;top:743px">‹&nbsp; Previous</span>
  <div class="abs" style="left:445px;top:750px;width:325px;height:2px;background:#d4d8de"></div>
  <div class="abs" style="left:445px;top:749px;width:45px;height:5px;background:var(--accent);border-radius:2px"></div>
  <span class="pager" style="left:800px;top:743px">Next &nbsp;›</span>
  <span class="pager center-text" style="top:770px">1 / 5</span>
</section>

<section class="cta" role="img" aria-label="Pale blue overlay on a pool terrace with pavilion">
  <h2 class="center-text" style="top:100px;font-size:40px;line-height:1;font-weight:900;color:var(--white)">READY TO REDEFINE LUXURY LIVING?</h2>
  <div class="rule" style="left:572px;top:148px;width:58px;background:var(--white)"></div>
  <p class="center-text" style="top:182px;font-size:18px;line-height:29px;color:var(--white)">Partner with Coral Basins to design a masterpiece that reflects your<br>lifestyle. Begin your journey toward timeless design, unmatched<br>craftsmanship, and true luxury.</p>
  <a class="btn btn--navy" style="left:501px;top:305px;width:198px;height:41px">Start Your Project</a>
</section>

<section class="reviews">
  <h2 class="heading" style="left:110px;top:108px;font-size:42px">What Our Customers Say</h2>
  <div class="rule" style="left:112px;top:157px;width:56px"></div>
  <div class="arrow" style="left:1002px;top:113px"><svg width="32" height="32"><path d="M19 10 L13 16 L19 22" stroke="#fff" stroke-width="2.5" fill="none"/></svg></div>
  <div class="arrow" style="left:1053px;top:113px"><svg width="32" height="32"><path d="M13 10 L19 16 L13 22" stroke="#fff" stroke-width="2.5" fill="none"/></svg></div>
  <p class="abs" style="left:110px;top:190px;font-size:16px;color:var(--muted)">Our pools don’t just transform spaces — they redefine lifestyles.</p>
  <article class="review" style="left:112px">
    <p>Lorem ipsum dolor sit amet, consectetur adipiscing elit, sed do eiusmod tempor incididunt ut labore et dolore magna aliqua. Quis ipsum suspendisse gravida. Risus commodo viverra maecenas vel facilisis.</p>
    <div class="avatar" role="img" aria-label="Customer portrait"></div>
    <span class="review__name">Mara Ellis</span><span class="review__role">lorem ipsum</span>
  </article>
  <article class="review" style="left:619px">
    <p>Lorem ipsum dolor sit amet, consectetur adipiscing elit, sed do eiusmod tempor incididunt ut labore et dolore magna aliqua. Quis ipsum suspendisse gravida. Risus commodo viverra maecenas vel facilisis.</p>
    <div class="avatar" role="img" aria-label="Customer portrait"></div>
    <span class="review__name">Mara Ellis</span><span class="review__role">lorem ipsum</span>
  </article>
  <article class="review" style="left:1123px">
    <p>Lorem ipsum dolor sit amet, consectetur adipiscing elit, sed do eiusmod tempor incididunt ut labore et dolore magna aliqua. Quis ipsum suspendisse gravida. Risus commodo viverra maecenas vel facilisis.</p>
    <div class="avatar" role="img" aria-label="Customer portrait"></div>
  </article>
</section>

<section class="gallery">
  <h2 class="heading center-text" style="top:54px;font-size:42px">Our Masterpiece</h2>
  <div class="rule" style="left:572px;top:105px;width:58px"></div>
  <p class="center-text" style="top:132px;font-size:16px;line-height:26px;color:var(--muted)">A curated showcase of exquisite designs that embody luxury, precision,<br>and tranquility.</p>
  <div class="photo" role="img" aria-label="Illuminated pool with arching water jets on a terrace" style="left:110px;top:213px;width:643px;height:279px;background:linear-gradient(180deg,#6a5a4a 0%,#2f6fd9 55%,#c9c2b6 100%)"></div>
  <div class="photo" role="img" aria-label="Modern pavilion with lit interior beside a pool at dusk" style="left:779px;top:213px;width:309px;height:279px;background:linear-gradient(180deg,#5a4c46 0%,#8a6a55 45%,#3b8fb3 100%)"></div>
  <div class="photo" role="img" aria-label="Contemporary home with pool at twilight" style="left:110px;top:522px;width:307px;height:278px;background:linear-gradient(180deg,#8fa0b2 0%,#5a5a5a 45%,#3fb0c4 100%)"></div>
  <div class="photo" role="img" aria-label="White modern villa with long pool and garden" style="left:445px;top:522px;width:643px;height:278px;background:linear-gradient(180deg,#b7cbdc 0%,#e7e7e7 40%,#3d7eaa 75%,#cfcfcf 100%)"></div>
  <a class="btn btn--navy" style="left:501px;top:839px;width:198px;height:42px">View Full Gallery</a>
</section>

<footer class="site-footer">
  <h4 class="foot-h" style="left:110px">About Us</h4>
  <p class="foot-l" style="left:110px;top:156px;width:260px;font-size:13px;line-height:24px">Excepteur sint occaecat cupidatat non proident, sunt in culpa qui officia illum dolore eu fugiat deserunt mollit anim id est laborum.</p>
  <span class="social is-active" style="left:112px" aria-label="Social link"></span>
  <span class="social" style="left:167px" aria-label="Social link"></span>
  <span class="social" style="left:213px" aria-label="Social link"></span>
  <span class="social" style="left:259px" aria-label="Social link"></span>
  <span class="social" style="left:305px" aria-label="Social link"></span>

  <h4 class="foot-h" style="left:439px">Main Links</h4>
  <span class="foot-l" style="left:439px;top:157px">Home</span>
  <span class="foot-l" style="left:439px;top:195px">About Us</span>
  <span class="foot-l" style="left:439px;top:233px">Services</span>
  <span class="foot-l" style="left:439px;top:272px">Gallery</span>
  <span class="foot-l" style="left:439px;top:310px">Contact Us</span>

  <h4 class="foot-h" style="left:648px">Contact Us</h4>
  <svg class="abs" style="left:648px;top:158px" width="18" height="22" viewBox="0 0 18 22"><path d="M9 21s-7-7.5-7-12a7 7 0 0 1 14 0c0 4.5-7 12-7 12z" fill="none" stroke="#fff" stroke-width="1.5"/><circle cx="9" cy="9" r="2.5" fill="none" stroke="#fff" stroke-width="1.5"/></svg>
  <span class="foot-l" style="left:688px;top:157px;line-height:26px">123, Coral Basins<br>Company Na 1236.</span>
  <svg class="abs" style="left:648px;top:244px" width="18" height="18" viewBox="0 0 18 18"><path d="M3 2h4l2 4-2.5 1.5a10 10 0 0 0 4 4L12 9l4 2v4a2 2 0 0 1-2 2A14 14 0 0 1 1 4a2 2 0 0 1 2-2z" fill="none" stroke="#fff" stroke-width="1.4"/></svg>
  <span class="foot-l" style="left:688px;top:246px">+ 1 555 014 2290</span>
  <svg class="abs" style="left:648px;top:313px" width="20" height="14" viewBox="0 0 20 14"><rect x="1" y="1" width="18" height="12" fill="none" stroke="#fff" stroke-width="1.4"/><path d="M1 1l9 7 9-7" fill="none" stroke="#fff" stroke-width="1.4"/></svg>
  <span class="foot-l" style="left:688px;top:310px">info@coralbasins.com</span>

  <h4 class="foot-h" style="left:955px">Other Links</h4>
  <span class="foot-l" style="left:955px;top:157px">Help</span>
  <span class="foot-l" style="left:955px;top:195px">Support</span>
  <span class="foot-l" style="left:955px;top:233px">Cookies Policy</span>
  <span class="foot-l" style="left:955px;top:272px">Terms &amp; Conditions</span>
  <span class="foot-l" style="left:955px;top:310px">Privacy Policy</span>

  <div class="abs" style="left:110px;top:406px;width:978px;height:1px;background:rgba(255,255,255,.2)"></div>
  <p class="center-text" style="top:428px;font-size:12px;color:var(--white)">Copyright © 2025 Coral Basins. All rights reserved.</p>
</footer>

</body>
</html>
```